Corporate Business Card

Very professional, Modern, Not to busy, include phone address email, website
(253) 617-4930, 18761 52nd Avenue S, Kent, WA 98047, martin@plumlinegroup.com, varkoworks.com

Target Market(s)

Manufacturing

Industry/Entity Type

Aero, machining, manufacturing, Off road racing

Contact Information for Business Card

Phone, address email, website

```html
<!DOCTYPE html>
<html lang="en">
<head>
<meta charset="utf-8">
<title>Varko Works — Business Card</title>
<link rel="stylesheet" href="https://fonts.googleapis.com/css2?family=Lato:wght@400;700&family=Oswald:wght@500&display=swap">
<style>
  :root {
    --backdrop: #1c1c1e;
    --card: #111113;
    --brand-blue: #1b3a7a;
    --accent-red: #d4202e;
    --ink-light: #f2f2f2;
    --divider: #6b6b6b;
  }
  * { margin: 0; padding: 0; box-sizing: border-box; }
  html, body {
    width: 1200px; height: 900px; overflow: hidden;
    background: var(--backdrop);
  }
  .canvas {
    position: relative; width: 1200px; height: 900px;
    display: flex; flex-direction: column; align-items: center; justify-content: center;
    gap: 50px;
  }
  .card {
    position: relative; width: 580px; height: 330px;
    background: var(--card);
    box-shadow: 0 10px 24px rgba(0,0,0,.55);
    overflow: hidden;
  }
  .card__band {
    position: absolute; left: 0; right: 0; bottom: 0; height: 11px;
    background: var(--brand-blue);
  }

  /* Front */
  .card--front { display: flex; align-items: center; justify-content: center; }
  .brand {
    display: flex; align-items: center; gap: 14px;
    margin-bottom: 30px;
  }
  .brand__square { width: 22px; height: 22px; background: var(--accent-red); }
  .brand__name {
    font-family: 'Lato', sans-serif; font-weight: 700;
    font-size: 52px; letter-spacing: 3px; text-transform: uppercase;
    color: var(--brand-blue);
  }

  /* Back */
  .identity {
    position: absolute; left: 70px; top: 118px; text-align: right; width: 210px;
  }
  .identity__name {
    font-family: 'Oswald', sans-serif; font-weight: 500;
    font-size: 31px; line-height: 1; text-transform: uppercase;
    color: var(--brand-blue); letter-spacing: .3px;
  }
  .identity__title {
    font-family: 'Lato', sans-serif; font-size: 16px;
    color: var(--accent-red); margin-top: 2px;
  }
  .divider {
    position: absolute; left: 300px; top: 110px; width: 1px; height: 88px;
    background: var(--divider);
  }
  .contact-list {
    position: absolute; left: 322px; top: 116px; list-style: none;
    font-family: 'Lato', sans-serif; font-size: 16px; color: var(--ink-light);
  }
  .contact-list li { display: flex; align-items: center; gap: 9px; height: 26px; }
  .icon { width: 15px; height: 15px; fill: var(--brand-blue); flex: none; }
  .address {
    position: absolute; left: 70px; top: 250px;
    display: flex; align-items: center; gap: 9px;
    font-family: 'Lato', sans-serif; font-size: 17px; color: var(--ink-light);
  }
</style>
</head>
<body>
<main class="canvas">

  <section class="card card--front" aria-label="Card front">
    <div class="brand">
      <span class="brand__square"></span>
      <span class="brand__name">Varko Works</span>
    </div>
    <div class="card__band"></div>
  </section>

  <section class="card card--back" aria-label="Card back">
    <div class="identity">
      <h1 class="identity__name">Daniel Reyes</h1>
      <p class="identity__title">Managing Director</p>
    </div>
    <div class="divider"></div>
    <ul class="contact-list">
      <li>
        <svg class="icon" viewBox="0 0 24 24"><path d="M6.6 10.8a15.1 15.1 0 0 0 6.6 6.6l2.2-2.2a1 1 0 0 1 1-.25 11.4 11.4 0 0 0 3.6.57 1 1 0 0 1 1 1V20a1 1 0 0 1-1 1A17 17 0 0 1 3 4a1 1 0 0 1 1-1h3.5a1 1 0 0 1 1 1c0 1.25.2 2.45.57 3.57a1 1 0 0 1-.25 1z"/></svg>
        (253) 617-4930
      </li>
      <li>
        <svg class="icon" viewBox="0 0 24 24"><path d="M2 5h20v14H2z M2 5l10 8 10-8" fill="none" stroke="#1b3a7a" stroke-width="2.4"/></svg>
        martin@plumlinegroup.com
      </li>
      <li>
        <svg class="icon" viewBox="0 0 24 24"><g fill="none" stroke="#1b3a7a" stroke-width="2"><circle cx="12" cy="12" r="10"/><ellipse cx="12" cy="12" rx="4.5" ry="10"/><path d="M2 12h20M4 7h16M4 17h16"/></g></svg>
        www.varkoworks.com
      </li>
    </ul>
    <p class="address">
      <svg class="icon" viewBox="0 0 24 24"><path d="M12 2a7 7 0 0 0-7 7c0 5.2 7 13 7 13s7-7.8 7-13a7 7 0 0 0-7-7zm0 9.5A2.5 2.5 0 1 1 12 6.5a2.5 2.5 0 0 1 0 5z"/></svg>
      18761 52nd Avenue S, Kent, WA 98047
    </p>
    <div class="card__band"></div>
  </section>

</main>
</body>
</html>
```